Biz Card Design TVCP

New business card for a new company.
Logo was completed by a designer on ArtHarbor and looking to continue requesting additional services.
Company Name: Tidal Vector Power Consulting
Although this company is starting in Canada, we will be moving towards a global presence within the next 6 months.
Key elements to this business are as follows.
Energy Procurement
Energy Reduction Services
Demand Side Consulting
Energy Efficiency Consulting
Saving Clients Money
Helping Them Go "Green"
Managing Their Energy Requirements
Basically the goal for our company is to find the best procurement solution for our clients and reduce their energy consumption. This reduces their expenses and the amount of greenhouse gas they produce on a daily basis.
I have been in the energy footprint for the last 20 years and know that most companies are looking to "do whatever is necessary to get them to sign on the dotted line". I would prefer to walk away from a client that I can't help than to put them into a situation that they will regret for years to come. This is where the "TIDAL" part of the company name comes from.
The following is a catch phrase that encompasses what we do.
"Reducing your carbon footprint & energy bill at the same time!"
The back of the card needs to have this statement along with some sort of illustration. The back is a playground for creative ideas.
The front of the card needs the following.
Logo.
First & Last Name (Gus Marwick)
Title (Energy Warrior)
Phone Number (555) 314-2718
Fax Number (555) 271-8314
Email Address gus@tidalvectorpowerconsulting.example
Address 47 fenwick rd Toronto Ontario K4T 2P9
I want it to be a card that is remembered when any of my staff give it to a customer. It HAS to stand out.
Target Market(s)
Business Owners, Decision Makers, 30 to 65+
Industry/Entity Type
Business
Look and feel

```html
<!DOCTYPE html>
<html lang="en">
<head>
<meta charset="utf-8">
<title>Tidal Vector Power Consulting — Business Card</title>
<link href="https://fonts.googleapis.com/css2?family=Open+Sans:ital,wght@0,400;0,600;0,700;1,400&display=swap" rel="stylesheet">
<style>
  :root {
    --bg: #eceae6;
    --navy: #1f4a8c;
    --blue: #2f62ad;
    --band-blue: #3d72bd;
    --green: #22a94b;
    --green-soft: #7cc576;
    --ink: #555a60;
    --white: #ffffff;
  }
  * { box-sizing: border-box; margin: 0; padding: 0; }
  html, body { width: 1200px; height: 900px; overflow: hidden; }
  body {
    background: var(--bg);
    font-family: "Open Sans", Arial, sans-serif;
    position: relative;
  }
  .card {
    position: absolute;
    width: 620px;
    height: 354px;
    border-radius: 4px;
    overflow: hidden;
    box-shadow: 0 8px 22px rgba(0,0,0,.22);
  }
  /* Back */
  .card-back { left: 60px; top: 80px; background: var(--navy); }
  .card-back .pattern {
    position: absolute; inset: 0 0 46px 0;
    background: radial-gradient(ellipse at 55% 40%, #3a6cb8 0%, #24518f 55%, #1b3f78 100%);
  }
  .card-back .brand {
    position: absolute; left: 0; right: 0; top: 128px;
    display: flex; align-items: center; justify-content: center; gap: 14px;
    color: var(--white); font-weight: 700; font-size: 30px; letter-spacing: -.5px;
  }
  .brand .mark { width: 34px; height: 34px; border-radius: 50%; background: currentColor; }
  .card-back .tagline-band {
    position: absolute; left: 0; right: 0; bottom: 0; height: 46px;
    background: var(--band-blue);
    display: flex; align-items: center; justify-content: center;
    color: var(--white); font-size: 17px; letter-spacing: .2px;
  }
  /* Front */
  .card-front { left: 520px; top: 470px; background: var(--white); }
  .card-front .swoosh { position: absolute; inset: 0; }
  .card-front .brand {
    position: absolute; left: 34px; top: 40px;
    display: flex; align-items: center; gap: 10px;
    color: var(--blue); font-weight: 700; font-size: 20px; letter-spacing: -.3px;
  }
  .card-front .brand .mark { width: 26px; height: 26px; background: var(--green-soft); border-radius: 50%; }
  .identity { position: absolute; left: 34px; top: 190px; }
  .identity .name { color: var(--green); font-weight: 700; font-size: 21px; }
  .identity .title { color: var(--blue); font-weight: 600; font-size: 14px; }
  .identity .address { color: var(--ink); font-size: 14px; line-height: 1.45; margin-top: 4px; }
  .contact {
    position: absolute; left: 34px; top: 96px;
    font-size: 13px; color: var(--ink); line-height: 1.6;
  }
  .contact .label { color: var(--green); }
</style>
</head>
<body>

<section class="card card-back" aria-label="Business card back">
  <div class="pattern" role="img" aria-label="Repeating faint dollar-sign pattern on blue"></div>
  <div class="brand"><span class="mark"></span>Tidal Vector Power Consulting</div>
  <div class="tagline-band">"Reducing your carbon footprint &amp; energy bill at the same time!"</div>
</section>

<section class="card card-front" aria-label="Business card front">
  <svg class="swoosh" viewBox="0 0 620 354" preserveAspectRatio="none" aria-hidden="true">
    <path d="M620 60 C590 190 520 300 420 354 L620 354 Z" fill="var(--band-blue)"/>
    <path d="M300 354 C380 330 440 300 480 250 L510 354 Z" fill="var(--green)"/>
    <path d="M400 300 C500 250 570 170 606 52 L620 40 C590 170 520 260 400 300 Z" fill="var(--green)"/>
  </svg>

  <div class="brand"><span class="mark"></span>Tidal Vector Power Consulting</div>

  <div class="contact">
    <div><span class="label">Phone :</span> (555) 314-2718</div>
    <div><span class="label">Fax :</span> (555) 271-8314</div>
    <div>gus@tidalvectorpowerconsulting.example</div>
  </div>

  <div class="identity">
    <div class="name">Gus Marwick <span class="title">| Energy Warrior</span></div>
    <div class="address">47 fenwick rd Toronto<br>Ontario K4T 2P9</div>
  </div>
</section>

</body>
</html>
```